Corvana Tongue Works, LLC

We need a business card that includes information about our business and conveys a reliable business that provides document translation services and interpreters for a variety of corporate and individual clients. We want to come across as professional, reliable, yet approachable. It should include the following on one side:

ESL / ENL Language Classes, Private Lessons, and Online Tutors
PLEXA Training and Testing
Translating & Interpreting Services
Contact us about Over-the-Phone Interpreting in over 200 languages
24/7/365
www.corvanatongue.example

The other side should include (555) 481-3062

Rhoda Pelling, President
482 Garnet Ave., Ste. 219
Indianapolis, IN 40917

Please add USA as part of the address. Also, please add rmpelling@corvanatongueworks.example as the e-mail address. Thank you.

Target Market(s)

Business professionals, their families, the international community

Industry/Entity Type

Business

Contact Information for Business Card

24/7/365
www.corvanatongue.example

(555) 481-3062

Rhoda Pelling, President
482 Garnet Ave., Ste. 219
Indianapolis, IN 40917
USA

Font styles to use
Sans Serif

Colors

Designer to choose colors to be used in the design.

Requirements
Must have
• See project description
• e-mail address and web address
• Phone number
Nice to have
• a globe
• physical address
Should not have
• Should not have the same color scheme as other agencies in our market in Indiana unless it is blue and black. No purple or yellow.

```html
<!DOCTYPE html>
<html lang="en">
<head>
<meta charset="utf-8">
<title>Corvana Tongue Works, LLC — Business Card</title>
<link rel="stylesheet" href="https://fonts.googleapis.com/css2?family=Montserrat:wght@400;500;600&family=Open+Sans:wght@400;600&display=swap">
<style>
  :root {
    --backdrop: #3a3532;
    --card-black: #0b0b0c;
    --card-edge: #1c1c1e;
    --brand-blue: #2a95d6;
    --text-white: #f4f6f8;
  }
  * { box-sizing: border-box; margin: 0; padding: 0; }
  html, body { width: 1200px; height: 930px; overflow: hidden; }
  body {
    background: var(--backdrop);
    font-family: "Open Sans", sans-serif;
    color: var(--text-white);
    position: relative;
  }
  .card {
    position: absolute;
    left: 290px;
    width: 620px;
    height: 354px;
    border-radius: 14px;
    background: linear-gradient(135deg, var(--card-black) 0%, var(--card-edge) 55%, var(--card-black) 100%);
    box-shadow: 0 14px 30px rgba(0,0,0,0.45);
    overflow: hidden;
  }
  .card--services { top: 76px; }
  .card--contact { top: 500px; }

  .brand { position: absolute; display: flex; align-items: center; gap: 14px; }
  .brand__dot {
    border-radius: 50%;
    background: var(--brand-blue);
    border: 4px solid var(--card-black);
    box-shadow: 0 0 0 2px var(--brand-blue);
    flex: none;
  }
  .brand__name {
    font-family: "Montserrat", sans-serif;
    font-weight: 500;
    color: var(--text-white);
    line-height: 1.05;
  }
  .card--services .brand { left: 140px; top: 40px; }
  .card--services .brand__dot { width: 92px; height: 92px; }
  .card--services .brand__name { font-size: 30px; }

  .services {
    position: absolute; left: 0; right: 0; top: 168px;
    text-align: center; font-size: 13.5px; line-height: 19px;
  }
  .services__rule {
    position: absolute; left: 60px; right: 60px; top: 256px;
    height: 2px; background: var(--brand-blue);
  }
  .services__contact {
    position: absolute; left: 0; right: 0; top: 268px;
    text-align: center; font-size: 13.5px; line-height: 19px; font-weight: 600;
  }

  .card--contact .brand { left: 44px; top: 48px; }
  .card--contact .brand__dot { width: 96px; height: 96px; }
  .card--contact .brand__name { font-size: 28px; }

  .person { position: absolute; right: 74px; top: 108px; text-align: right; }
  .person__name {
    font-family: "Montserrat", sans-serif; font-weight: 500;
    font-size: 26px; letter-spacing: 0.5px; color: var(--brand-blue);
    text-transform: uppercase;
  }
  .person__title { font-size: 14px; margin-top: 6px; }
  .person__rule {
    position: absolute; left: 150px; right: 74px; top: 146px;
    height: 2px; background: var(--brand-blue);
  }
  .accent-bars { position: absolute; right: 36px; top: 104px; display: flex; gap: 5px; }
  .accent-bars span { display: block; height: 40px; }
  .accent-bars .bar-white { width: 4px; background: var(--text-white); }
  .accent-bars .bar-blue { width: 16px; background: var(--brand-blue); }

  .contact-list {
    position: absolute; left: 48px; top: 218px;
    list-style: none; font-size: 15px; line-height: 24px;
  }
  .contact-list li { display: flex; align-items: center; gap: 10px; }
  .contact-list svg { width: 13px; height: 13px; flex: none; }

  .address {
    position: absolute; right: 40px; top: 208px;
    text-align: right; font-size: 15px; line-height: 22px;
  }
  .swoosh { position: absolute; left: 0; bottom: 0; width: 620px; height: 80px; }
</style>
</head>
<body>

<section class="card card--services" aria-label="Services side">
  <div class="brand">
    <span class="brand__dot"></span>
    <p class="brand__name">Corvana<br>Tongue Works<br>LLC</p>
  </div>
  <div class="services">
    <p>ESL / ENL Language Classes, Private Lessons, and Online Tutors</p>
    <p>PLEXA Training and Testing</p>
    <p>Translating &amp; Interpreting Services</p>
  </div>
  <div class="services__rule"></div>
  <div class="services__contact">
    <p>Contact us about Over-the-Phone Interpreting in over 200 languages</p>
    <p>24/7/365</p>
  </div>
</section>

<section class="card card--contact" aria-label="Contact side">
  <div class="brand">
    <span class="brand__dot"></span>
    <p class="brand__name">Corvana<br>Tongue Works<br>LLC</p>
  </div>

  <div class="person__rule"></div>
  <div class="person">
    <p class="person__name">Rhoda Pelling</p>
    <p class="person__title">President</p>
  </div>
  <div class="accent-bars"><span class="bar-white"></span><span class="bar-blue"></span></div>

  <ul class="contact-list">
    <li>
      <svg viewBox="0 0 16 16" aria-hidden="true"><path fill="#2a95d6" d="M3.6 1.2l2.3 2.7-1.3 1.8c.9 2 2.6 3.8 4.6 4.7l1.8-1.3 2.7 2.3-1.4 2.4C7 13.6 2.4 9 1.2 3.6z"/></svg>
      (555) 481-3062
    </li>
    <li>
      <svg viewBox="0 0 16 16" aria-hidden="true"><rect x="1.5" y="3.5" width="13" height="9" fill="none" stroke="#2a95d6" stroke-width="1.6"/><path d="M1.5 3.5L8 9l6.5-5.5" fill="none" stroke="#2a95d6" stroke-width="1.6"/></svg>
      rmpelling@corvanatongueworks.example
    </li>
    <li>
      <svg viewBox="0 0 16 16" aria-hidden="true"><circle cx="8" cy="8" r="6.5" fill="none" stroke="#2a95d6" stroke-width="1.4"/><ellipse cx="8" cy="8" rx="2.8" ry="6.5" fill="none" stroke="#2a95d6" stroke-width="1.2"/><path d="M1.5 8h13M2.6 4.6h10.8M2.6 11.4h10.8" stroke="#2a95d6" stroke-width="1.1"/></svg>
      www.corvanatongue.example
    </li>
  </ul>

  <div class="address">
    <p>482 Garnet Ave., Ste. 219</p>
    <p>Indianapolis, IN 40917 USA</p>
  </div>

  <svg class="swoosh" viewBox="0 0 620 80" preserveAspectRatio="none" aria-hidden="true">
    <path d="M0 70 L360 70 C395 70 405 32 440 32 L620 32 L620 80 L0 80 Z" fill="#2a95d6"/>
    <path d="M0 62 L352 62 C386 62 396 26 430 26 L620 26" fill="none" stroke="#f4f6f8" stroke-width="4"/>
  </svg>
</section>

</body>
</html>
```